New Webpage for High Class Expert Witness Services Company

We are looking for a minimalist design for a webpage that just has our logo and an entry form offer to connect with one of our Liaisons.
The entry form should just ask for Name, Email, Contact Info and Description of Project.

Company Name is: The Marlowe Crest Advisory Services

Number of Pages Required

1 page

```html
<!DOCTYPE html>
<html lang="en">
<head>
<meta charset="UTF-8">
<title>Marlowe Crest Advisory Services – Connect with a Liaison</title>
<link href="https://fonts.googleapis.com/css2?family=Playfair+Display:wght@400;500;700&family=Roboto:wght@400&display=swap" rel="stylesheet">
<style>
  :root {
    --page-bg: #131313;
    --panel-bg: #161616;
    --silver: #c4c4c4;
    --white: #ffffff;
    --frame: #b9b9b9;
    --field-bg: #ffffff;
    --placeholder: #a3a3a3;
    --button-bg: #c1c2c3;
    --button-text: #1e1e1e;
    --footer-text: #cfcfcf;
    --below: #ffffff;
  }
  * { box-sizing: border-box; margin: 0; padding: 0; }
  html, body {
    width: 1200px; height: 2624px; overflow: hidden;
    background: var(--below);
  }
  .page {
    position: relative; width: 1200px; height: 2556px;
    background: var(--page-bg);
  }
  .brand-panel {
    position: absolute; left: 128px; top: 63px; width: 944px; height: 454px;
    background: var(--panel-bg);
    display: flex; align-items: center; justify-content: center; gap: 22px;
  }
  .brand-mark { width: 44px; height: 44px; background: var(--silver); }
  .brand-name {
    font-family: "Playfair Display", serif; font-weight: 400;
    font-size: 44px; color: var(--silver); letter-spacing: 1px;
    text-transform: uppercase;
  }
  .headline {
    position: absolute; left: 128px; top: 556px; width: 944px;
    text-align: center; font-family: "Playfair Display", serif; font-weight: 500;
    font-size: 70px; line-height: 66px; color: var(--silver);
    text-transform: uppercase; letter-spacing: -1px;
  }
  .intro {
    position: absolute; left: 128px; top: 737px; width: 944px;
    font-family: "Roboto", sans-serif; font-size: 34px; line-height: 51px;
    color: var(--white); text-align: justify;
  }
  .liaison-form {
    position: absolute; left: 128px; top: 1066px; width: 944px; height: 1002px;
    border: 1.5px solid var(--frame); border-radius: 47px;
  }
  .field-label {
    position: absolute; left: 77px;
    font-family: "Playfair Display", serif; font-weight: 700;
    font-size: 32px; line-height: 40px; color: var(--white);
    text-transform: uppercase; letter-spacing: -0.5px;
  }
  .field {
    position: absolute; left: 77px; width: 790px; height: 84px;
    background: var(--field-bg); border: none; border-radius: 4px;
    padding: 0 35px; font-family: "Roboto", sans-serif; font-size: 29px;
    color: #222;
  }
  .field::placeholder { color: var(--placeholder); }
  textarea.field { height: 200px; padding: 26px 30px; resize: vertical; }
  .submit-button {
    position: absolute; left: 77px; top: 843px; width: 790px; height: 83px;
    background: var(--button-bg); border: none; border-radius: 4px;
    font-family: "Playfair Display", serif; font-size: 32px; color: var(--button-text);
  }
  .footer-note {
    position: absolute; left: 128px; top: 2218px; width: 944px;
    text-align: center; font-family: "Playfair Display", serif;
    font-variant: small-caps; font-size: 38px; line-height: 52px;
    color: var(--footer-text);
  }
</style>
</head>
<body>
<main class="page">
  <header class="brand-panel">
    <span class="brand-mark"></span>
    <span class="brand-name">Marlowe Crest Advisory Services</span>
  </header>

  <h1 class="headline">Connect with one of<br>our liaisons</h1>

  <p class="intro">Lorem ipsum dolor sit amet, consectetur adipiscing elit, sed do eiusmod tempor incididunt ut labore et dolore magna aliqua. Vulputate dignissim suspendisse in est ante. Faucibus turpis in eu mi bibendum neque. Sodales ut etiam sit amet nisl purus. Velit laoreet id donec ultrices tincidunt.</p>

  <form class="liaison-form">
    <label class="field-label" for="name" style="top:73px">Name</label>
    <input class="field" id="name" type="text" placeholder="Name" style="top:132px">

    <label class="field-label" for="email" style="top:235px">Email</label>
    <input class="field" id="email" type="email" placeholder="Type your Email" style="top:295px">

    <label class="field-label" for="contact" style="top:398px">Contact Info</label>
    <input class="field" id="contact" type="text" placeholder="Type your contact information" style="top:457px">

    <label class="field-label" for="project" style="top:560px">Description of Project</label>
    <textarea class="field" id="project" placeholder="Describe about your project." style="top:619px"></textarea>

    <button class="submit-button" type="submit">SUBMIT</button>
  </form>

  <footer class="footer-note">Copyright © 2026 &amp; Powered by The Marlowe Crest<br>Advisory Services</footer>
</main>
</body>
</html>
```